Mental Health Therapy Website

I need a design for a mental health therapy website. It is a private practice. The business name is Fenwick Counseling, PLLC. My name is Martin Fenwick, LMHC, NCC, DCC. I would like some of the features/menus to be Home; Welcome/About Me, Rates and Services, Common Questions, and Contact.
If possible I would like a blog on the main page that I can update with articles I write. I would like the contact page to feature a map to my location (4189 Birchmont Ave. S, Lakewood, WA 98312).
I would like to place a small photo of me on the Welcome/About page.
I am new to this so if I am forgetting anything, please ask me!!
I will upload my logo so you can fit it and the color scheme into the design.
Thank you so very much!

```html
<!DOCTYPE html>
<html lang="en">
<head>
<meta charset="utf-8">
<title>Fenwick Counseling, PLLC</title>
<link href="https://fonts.googleapis.com/css2?family=Noto+Sans:wght@400;700&family=Noto+Serif:wght@400;700&display=swap" rel="stylesheet">
<style>
  :root {
    --blue: #34679b;
    --blue-nav: #3d6b9e;
    --green: #73a23a;
    --text: #6b6b6b;
    --muted: #8e8e8e;
    --panel: #f0f0f0;
    --tint: #dde9d0;
    --white: #ffffff;
  }
  * { box-sizing: border-box; margin: 0; padding: 0; }
  html, body { width: 1200px; height: 820px; overflow: hidden; }
  body {
    background: linear-gradient(to bottom, var(--white) 0, var(--white) 109px, var(--tint) 110px, var(--white) 265px, var(--white) 100%);
    font-family: "Noto Sans", sans-serif;
    color: var(--text);
    position: relative;
  }
  .site-header {
    height: 109px;
    background: var(--white);
    position: relative;
  }
  .brand {
    position: absolute; left: 109px; top: 22px;
    display: flex; align-items: center; gap: 12px;
    font-family: "Noto Serif", serif;
    font-weight: 700;
    font-size: 25px;
    color: var(--blue);
  }
  .brand-mark {
    width: 46px; height: 46px; border-radius: 50%;
    background: var(--green);
  }
  .main-nav {
    position: absolute; right: 109px; top: 37px;
    display: flex; gap: 0;
    font-family: "Noto Serif", serif;
    font-weight: 700;
    font-size: 16px;
  }
  .main-nav a {
    display: block; text-decoration: none;
    color: var(--green);
    padding: 10px 12px 11px;
    margin-left: 10px;
  }
  .main-nav a.active { background: var(--blue-nav); color: var(--white); }
  .main-nav a:last-child { padding-right: 0; }
  .blog {
    position: absolute; left: 109px; top: 143px; width: 595px;
  }
  .post { margin-bottom: 14px; }
  .post-title {
    font-family: "Noto Serif", serif;
    font-weight: 700;
    font-size: 27px;
    color: var(--blue);
    line-height: 1.3;
  }
  .post-date { font-size: 15px; color: var(--muted); margin: 6px 0 4px; }
  .post p { font-size: 15px; line-height: 23px; margin-bottom: 23px; }
  .post .comments {
    font-size: 15px; font-weight: 700; color: var(--green);
    text-decoration: none; display: block; margin-top: -2px;
  }
  .sidebar {
    position: absolute; left: 753px; top: 144px; width: 338px;
  }
  .about-card {
    background: var(--panel);
    padding: 15px 6px 22px 14px;
  }
  .about-card h2 {
    font-family: "Noto Serif", serif;
    font-weight: 700; font-size: 15px;
    color: var(--green);
    margin-bottom: 12px;
  }
  .portrait {
    width: 291px; height: 229px;
    margin-left: 10px;
    border: 1px solid #9a9a9a;
    background: linear-gradient(135deg, #dfe3ec 0%, #c9ccd8 45%, #d7dbe6 100%);
  }
  .about-card p {
    font-size: 12px; line-height: 20.5px; margin-top: 10px;
  }
  .widget-title {
    font-family: "Noto Serif", serif;
    font-weight: 700; font-size: 21px;
    color: var(--green);
    margin: 22px 0 6px;
  }
  .latest-posts { list-style: none; }
  .latest-posts a {
    font-family: "Noto Serif", serif;
    font-size: 17.5px; line-height: 30.5px;
    color: var(--blue); text-decoration: none;
  }
  .social { display: flex; gap: 9px; margin-top: 8px; }
  .social span {
    width: 36px; height: 36px; border-radius: 5px; display: block;
  }
  .social .s1 { background: #2f5a96; }
  .social .s2 { background: #3a3a3a; }
  .social .s3 { background: #39b6e4; }
  .social .s4 { background: #1d7fb8; }
</style>
</head>
<body>
  <header class="site-header">
    <div class="brand"><span class="brand-mark"></span>Fenwick Counseling</div>
    <nav class="main-nav">
      <a class="active" href="#">Home</a>
      <a href="#">About Me</a>
      <a href="#">Rates and Services</a>
      <a href="#">Common Questions</a>
      <a href="#">Contact</a>
    </nav>
  </header>

  <main class="blog">
    <article class="post">
      <h1 class="post-title">This is a blog post title</h1>
      <div class="post-date">22nd January 2014</div>
      <p>Lorem ipsum dolor sit amet, eius debitis scribentur ne vix, eu error deseruisse sed, dicat interesset in eam. Sea vide aliquando id. Vocent audire viderer mei at, sea at mucius labore dignissim. Mea virtute liberavisse et, at usu adhuc dolores qualisque. In qui tollit epicurei sadipscing, timeam prompta eligendi qui ea, ea duo harum pertinax. Cibo laboramus vix at.</p>
      <p>Ei vitae sanctus necessitatibus per. Omnis essent vivendum mel ne, ad nemore doctus integre usu. Per cu audire definitionem, ei facer vituperatoribus cum, eam in graeco maluisset. Has explicari urbanitas democritum no, sed sale mazim praesent eu, mundi alterum te sed.</p>
      <p>Est no diam agam sadipscing. Eum solet moderatius te, pri blandit ullamcorper ea. Dicat tempor debitis ne duo, ei nam recusabo argumentum. Ad qui laudem viderer discere. Semper facete accusata sit eu</p>
      <a class="comments" href="#">3 comments</a>
    </article>
    <article class="post">
      <h1 class="post-title">And another blog post title</h1>
      <div class="post-date">22nd January 2014</div>
      <p>Lorem ipsum dolor sit amet, eius debitis scribentur ne vix, eu error deseruisse sed, dicat interesset in eam. Sea vide aliquando id. Vocent audire viderer mei at, sea at mucius labore dignissim. Mea virtute liberavisse et, at usu adhuc dolores qualisque. In qui tollit epicurei sadipscing, timeam prompta eligendi qui ea, ea duo harum pertinax. Cibo laboramus vix at.</p>
      <p>Ei vitae sanctus necessitatibus per. Omnis essent vivendum mel ne, ad nemore doctus integre usu.</p>
    </article>
  </main>

  <aside class="sidebar">
    <section class="about-card">
      <h2>My name is Martin Fenwick, LMHC, NCC, DCC.</h2>
      <div class="portrait" role="img" aria-label="Portrait photo of Martin Fenwick"></div>
      <p>Est no diam agam sadipscing. Eum solet moderatius te, pri blandit ullamcorper ea. Dicat tempor debitis ne duo, ei nam recusabo argumentum. Ad qui laudem viderer discere. Semper facete accusata sit eu</p>
    </section>
    <h3 class="widget-title">Latest Posts</h3>
    <ul class="latest-posts">
      <li><a href="#">This is a blog post title</a></li>
      <li><a href="#">And another blog post title</a></li>
      <li><a href="#">Benefits on meditation</a></li>
      <li><a href="#">Symptoms of Depression</a></li>
      <li><a href="#">Yet another blog post depresssion</a></li>
    </ul>
    <h3 class="widget-title">Follow me on Social Media</h3>
    <div class="social">
      <span class="s1" role="img" aria-label="Social network link"></span>
      <span class="s2" role="img" aria-label="Social network link"></span>
      <span class="s3" role="img" aria-label="Social network link"></span>
      <span class="s4" role="img" aria-label="Social network link"></span>
    </div>
  </aside>
</body>
</html>
```